Website for a company offering full serivce charging solutions for electric cars

The company "tanu-werk" (english: "tanu-works") offering all-in-one-solutions for charging infrastructure for electric mobility.

There are four products:
1- Wallboxes for single-family homes
2- Solutions for property devloper/-management for property parking space
3- All-in-one-charging solution for municipalities/communities
4- Solutions for tourism/hotels/holiday appartments

The Website structure:
1. Main Page
2.1. Product Page Single Homes
2.2. Product Page Property Management / Parking
2.3. Product Page Municipality
2.4. Product Page Tourism
3. Contact Form / Request for information
4. Imprint / Legal

The Website should be built on Wordpress with a powerful possibility to simply add/modify specific landing pages.

We would like you to implement the website later and also maintain it if possible, but we would be able to do minor modifications by ourselfs (for A/B-Testing)

The website should be clear and simple, easy to understand.
Target group is mainly B2C without deeper knowledge of that topic.

It should suggest, that we will provide a very simple way to get the charging infrastructure done.

We need a contact form, maybe we will use Hubspot later.

Attached you will find a draft of the main page and a landing page (for 2.2) - it is just the content, please ignore the design. We would love to let you create a suitable design.
Also you will find some drafts a bit different for the same story.

I added also a few stock photos, but they don't need to be used! If you have better ideas, you are welcome!

Industry/Entity Type

Charging/Electric mobility

Number of Pages Required

2 page

Font styles to use
Sans Serif

Requirements
Must have
• Based on Wordpress, and the designer should be able to implement it on Wordpress on a later step

```html
<!DOCTYPE html>
<html lang="de">
<head>
<meta charset="utf-8">
<title>tanu-werk – Ladeinfrastruktur für Elektromobilität</title>
<link href="https://fonts.googleapis.com/css2?family=Oswald:wght@600;700&family=Montserrat:wght@400;500;600;700&family=Open+Sans:wght@400;600&display=swap" rel="stylesheet">
<style>
:root{
  --purple:#8a2be2;
  --magenta:#e0309a;
  --grad:linear-gradient(90deg,#8a2be2,#e0309a);
  --ink:#1d1d2b;
  --text:#4a4a55;
  --muted:#8a8a96;
  --grey:#efeff1;
  --navy:#111a2c;
  --white:#fff;
}
*{box-sizing:border-box;margin:0;padding:0}
html,body{width:1200px;height:3448px;overflow:hidden}
body{font-family:"Open Sans",sans-serif;color:var(--text);background:var(--white);position:relative}
.abs{position:absolute}
.brand{display:flex;align-items:center;gap:10px;font-family:"Montserrat",sans-serif;font-weight:700;color:var(--ink)}
.brand-dot{width:22px;height:22px;border-radius:50%;background:var(--magenta)}
.btn{display:inline-flex;align-items:center;gap:10px;height:38px;padding:0 22px 0 6px;border-radius:19px;background:var(--grad);color:#fff;font-family:"Montserrat",sans-serif;font-size:13px;font-weight:600;text-decoration:none}
.btn-icon{width:28px;height:28px;border-radius:50%;background:#fff;display:flex;align-items:center;justify-content:center}
/* header */
.site-header{position:absolute;top:0;left:0;width:1200px;height:60px;background:#fff;padding:0 160px;display:flex;align-items:center;justify-content:space-between}
.site-header .brand{font-size:22px}
.main-nav{display:flex;gap:28px;font-family:"Montserrat",sans-serif;font-size:13px;color:var(--ink)}
.main-nav a{color:inherit;text-decoration:none}
.main-nav .active{border-bottom:2px solid var(--magenta);padding-bottom:3px}
/* hero */
.hero{top:60px;left:0;width:1200px;height:700px;background:linear-gradient(100deg,#f4f5f8 0%,#e9ebf0 40%,#c9ccd6 70%,#8d92a3 100%)}
.hero-glow{right:170px;top:150px;width:220px;height:220px;border-radius:50%;background:radial-gradient(circle,#4aa8ff 0%,#1f6fd6 40%,rgba(31,111,214,0) 70%)}
.hero h1{left:160px;top:210px;width:560px;font-family:"Oswald",sans-serif;font-weight:700;font-size:40px;line-height:46px;color:var(--ink);text-transform:uppercase}
.hero .btn{left:160px;top:375px}
/* partner */
.logo-mark{left:570px;width:60px;height:26px;border:3px solid var(--magenta);border-radius:13px}
.section-title{width:1200px;text-align:center;font-family:"Montserrat",sans-serif;font-weight:700;color:var(--ink)}
.photo-circle{border-radius:50%;overflow:hidden}
.arc{border-radius:50%;border:6px solid transparent;border-left-color:var(--purple);border-bottom-color:var(--magenta)}
.arc-right{border-left-color:transparent;border-bottom-color:transparent;border-right-color:var(--purple);border-top-color:var(--magenta)}
.text-card{left:520px;top:890px;width:330px;height:330px;background:#fff;border-left:4px solid var(--magenta);box-shadow:0 6px 24px rgba(0,0,0,.08);padding:24px 22px;font-size:11.5px;line-height:18px}
.text-card p{margin-bottom:14px}
/* solutions */
.solutions{top:1330px;left:0;width:1200px;height:1710px;background:var(--grey)}
.solution h3{font-family:"Montserrat",sans-serif;font-weight:700;font-size:19px;color:var(--ink);margin-bottom:16px}
.solution ul{list-style:none}
.solution li{position:relative;padding-left:14px;font-size:11.5px;line-height:17px;margin-bottom:14px}
.solution li::before{content:"";position:absolute;left:0;top:6px;width:5px;height:5px;border-radius:50%;background:var(--magenta)}
.solution li.sub{padding-left:28px;margin-bottom:8px}
.solution li.sub::before{left:14px;background:var(--muted)}
/* contact band */
.contact-band{top:3040px;left:0;width:1200px;height:140px;background:var(--navy);display:flex;justify-content:space-between;padding:0 160px;align-items:center}
.contact-item{display:flex;align-items:center;gap:14px;color:#fff;width:280px}
.contact-icon{width:40px;height:40px;border-radius:50%;background:var(--grad);display:flex;align-items:center;justify-content:center}
.contact-item strong{display:block;font-family:"Montserrat",sans-serif;font-size:13px;font-weight:600}
.contact-item span{font-size:11.5px;color:#c9cbd6}
/* footer */
.site-footer{top:3180px;left:0;width:1200px;height:268px;background:#fff;text-align:center}
.footer-brand{justify-content:center;font-size:22px;margin-top:30px}
.footer-nav{display:flex;justify-content:center;gap:48px;margin-top:48px;font-family:"Montserrat",sans-serif;font-size:12px;color:var(--ink)}
.copyright{font-size:11px;color:var(--muted);margin-top:22px;border-top:1px solid #e4e4ea;padding-top:14px;width:880px;margin-left:160px}
.social{display:flex;justify-content:center;gap:16px;margin-top:18px}
.social span{width:30px;height:30px;border-radius:50%;background:var(--magenta)}
</style>
</head>
<body>

<header class="site-header">
  <div class="brand"><span class="brand-dot"></span>tanu-werk.de</div>
  <nav class="main-nav">
    <a class="active" href="#">Lösungen</a><a href="#">Unternehmen</a><a href="#">Dienstleistungen</a><a href="#">Karriere</a><a href="#">Kontakt</a>
  </nav>
</header>

<section class="hero abs" role="img" aria-label="Foto: Ladestecker an einem Elektroauto mit blau leuchtendem Ladeanschluss">
  <div class="hero-glow abs"></div>
  <h1 class="abs">All-in-One-Lösungen für Ladeinfrastruktur für Elektromobilität anzubieten</h1>
  <a class="btn abs" href="#"><span class="btn-icon"><svg width="14" height="14" viewBox="0 0 24 24"><path d="M5 12h14M13 6l6 6-6 6" stroke="#e0309a" stroke-width="3" fill="none"/></svg></span>Kontakt aufnehmen</a>
</section>

<div class="logo-mark abs" style="top:800px"></div>
<h2 class="section-title abs" style="top:832px;font-size:28px">tanu-werk ist Ihr Partner</h2>
<div class="arc abs" style="left:150px;top:920px;width:310px;height:310px"></div>
<div class="photo-circle abs" role="img" aria-label="Foto: Frau lädt ihr Elektroauto an einer Ladesäule" style="left:165px;top:935px;width:280px;height:280px;background:linear-gradient(135deg,#d9c6b4,#8b6b58 60%,#3d3a44)"></div>
<div class="text-card abs">
  <p>Wenn das Laden nicht nur einfach, sondern die Umsetzung auch aus einer Hand kommen soll: Wir bieten Lösungen sowohl für Privatkunden, Geschäfts- sowie an auch Kommunen an, die schnell, fair und ohne Eigenleistung zu einer smarten Ladelösung für E-Fahrzeuge kommen möchten.</p>
  <p>Von der Beratung über die Installation, Abrechnung bis zur Abrechnung und Wartung bekommen Sie bei uns alles aus einer Hand. Auf Wunsch vermieten wir auch die Ladetechnik und übernehmen im gewerblichen Bereich die direkte Abrechnung mit dem Nutzer.</p>
  <a class="btn" href="#"><span class="btn-icon"><svg width="14" height="14" viewBox="0 0 24 24"><path d="M5 12h14M13 6l6 6-6 6" stroke="#e0309a" stroke-width="3" fill="none"/></svg></span>Alle Ansehen</a>
</div>

<section class="solutions abs">
  <h2 class="section-title abs" style="top:40px;font-size:28px;line-height:36px">Fragen Sie Uns Nach Der Auf Ihre Individuellen<br>Bedürfnisse Zugeschnittenen Lösung</h2>

  <div class="solution abs" style="left:160px;top:160px;width:420px">
    <h3>Als Privatkunde</h3>
    <ul>
      <li>Bedarfsanalyse mit anfänglicher Beratung über die Möglichkeiten der Umsetzung</li>
      <li>Prüfung und Übernahme der Anmeldung verfügbarer Fördermöglichkeiten</li>
      <li>Auswahl an smarten Wallbox-Lösungen passend für Ihr Fahrzeug und Ihre Bedürfnisse</li>
      <li>Installation inkl. aller notwendigen Materialien und Tätigkeiten (Durchbrüche, Kabelzüge etc.)</li>
      <li>Elektrokontrolle und Anmeldung in der Ladetechnik</li>
      <li>Jährlich technische Wartung nach Bedarf</li>
    </ul>
    <a class="btn" href="#" style="margin-top:10px"><span class="btn-icon"><svg width="14" height="14" viewBox="0 0 24 24"><path d="M5 12h14M13 6l6 6-6 6" stroke="#e0309a" stroke-width="3" fill="none"/></svg></span>Alle Ansehen</a>
  </div>
  <div class="arc arc-right abs" style="left:610px;top:250px;width:310px;height:310px"></div>
  <div class="photo-circle abs" role="img" aria-label="Foto: modernes Einfamilienhaus mit Einfahrt" style="left:625px;top:265px;width:280px;height:280px;background:linear-gradient(160deg,#e8eef4,#c9c3b8 55%,#7d8a6a)"></div>

  <div class="arc abs" style="left:150px;top:590px;width:310px;height:310px"></div>
  <div class="photo-circle abs" role="img" aria-label="Foto: Geschäftsteam bei einer Besprechung am Tisch" style="left:165px;top:605px;width:280px;height:280px;background:linear-gradient(135deg,#f1e6da,#c8a98e 55%,#6e5a4c)"></div>
  <div class="solution abs" style="left:640px;top:740px;width:400px">
    <h3>Als Geschäftskunde</h3>
    <ul>
      <li>Durchführung einer individuellen Bedarfsanalyse inkl. Ermittlung der Anforderungen für</li>
      <li class="sub">Haus- und Immobilienverwaltungen</li>
      <li class="sub">Dienstleistungs- und Handelsunternehmen</li>
      <li class="sub">Hotels und Beherbergungsbetriebe</li>
      <li class="sub">Parkraum- und Parkhausbetreiber</li>
      <li class="sub">Tourismus, Sport- und Freizeiteinrichtungen</li>
      <li>Planung und Projektierung des Installationsaufwands inkl. Netzanschlusscheck</li>
      <li>Leasing oder Kauf der Hardware</li>
      <li>Normgerechte Installation der Ladeinfrastruktur mit Durchbruch-, Brandschutz- und Kabelarbeiten</li>
    </ul>
    <a class="btn" href="#"><span class="btn-icon"><svg width="14" height="14" viewBox="0 0 24 24"><path d="M5 12h14M13 6l6 6-6 6" stroke="#e0309a" stroke-width="3" fill="none"/></svg></span>Alle Ansehen</a>
  </div>

  <div class="solution abs" style="left:160px;top:1200px;width:420px">
    <h3>Als Kommune</h3>
    <ul>
      <li>Konzepterstellung möglicher Ladeinfrastrukturen innerhalb Ihrer Gemeinde</li>
      <li>Planung und Projektierung inkl. sämtlicher behördlicher Genehmigungsverfahren und Beantragung von Fördermitteln</li>
      <li>Fachgerechte Installation und Inbetriebnahme</li>
      <li>Regelmäßige Wartung gemäß Vorschrift</li>
      <li>Reparatur und Instandhaltung</li>
      <li>Direkte Abrechnung mit dem Nutzer</li>
      <li>Beteiligung der Gemeinde am Umsatz</li>
    </ul>
    <a class="btn" href="#"><span class="btn-icon"><svg width="14" height="14" viewBox="0 0 24 24"><path d="M5 12h14M13 6l6 6-6 6" stroke="#e0309a" stroke-width="3" fill="none"/></svg></span>Alle Ansehen</a>
  </div>
  <div class="arc arc-right abs" style="left:610px;top:1250px;width:310px;height:310px"></div>
  <div class="photo-circle abs" role="img" aria-label="Foto: historisches Rathausgebäude unter blauem Himmel" style="left:625px;top:1265px;width:280px;height:280px;background:linear-gradient(180deg,#8fb4dc,#c6d3e0 45%,#b9a58e 75%,#6d6a5e)"></div>
</section>

<section class="contact-band abs">
  <div class="contact-item"><span class="contact-icon"><svg width="18" height="18" viewBox="0 0 24 24"><path d="M6.6 10.8a15 15 0 0 0 6.6 6.6l2.2-2.2c.3-.3.7-.4 1-.2 1.1.4 2.3.6 3.6.6.6 0 1 .4 1 1V20c0 .6-.4 1-1 1A17 17 0 0 1 3 4c0-.6.4-1 1-1h3.5c.6 0 1 .4 1 1 0 1.3.2 2.5.6 3.6.1.3 0 .7-.2 1z" fill="#fff"/></svg></span><div><strong>Anruf</strong><span>0800 555 0142 (Gratis)</span></div></div>
  <div class="contact-item"><span class="contact-icon"><svg width="18" height="18" viewBox="0 0 24 24"><rect x="3" y="5" width="18" height="14" rx="2" fill="none" stroke="#fff" stroke-width="2"/><path d="M3 7l9 6 9-6" fill="none" stroke="#fff" stroke-width="2"/></svg></span><div><strong>Email</strong><span>info@tanu-werk.de</span></div></div>
  <div class="contact-item"><span class="contact-icon"><svg width="18" height="18" viewBox="0 0 24 24"><path d="M12 2a7 7 0 0 0-7 7c0 5 7 13 7 13s7-8 7-13a7 7 0 0 0-7-7zm0 9.5A2.5 2.5 0 1 1 12 6.5a2.5 2.5 0 0 1 0 5z" fill="#fff"/></svg></span><div><strong>Ein Kleid</strong><span>Musterweg 12, 54321 Beispielstadt</span></div></div>
</section>

<footer class="site-footer abs">
  <div class="brand footer-brand"><span class="brand-dot"></span>tanu-werk.de</div>
  <nav class="footer-nav"><span>AGB</span><span>Datenschutzerklärung</span><span>Impressum</span><span>Kontakt</span><span>Karriere</span><span>FAQs</span></nav>
  <p class="copyright">Urheberrecht © 2022 tanu-werk.de. Alle Rechte vorbehalten.</p>
  <div class="social"><span></span><span></span><span></span></div>
</footer>

</body>
</html>
```